Production Company need business cards

Hello ! I need a business card for my production company called Brightlane. I put the logo in the files ! This is a brand new production company, modern. We work in the digital industry and have a new and young vision of the content creation. I'll use this business card with a system integrated in it, it will be a digital business card (the type of business card you put behind a phone, and in the phone all your informations will be displayed. You need to respect the colors of the logo for the card (but you can interchange the logo colours to use a black card, or white card, or gold card... You have the .ai file in the files)
In the uploaded files, i puted 2 business card examples, you can see on the cards I just need at the back a small square for a QR code (you can fake it for now).
Target Market(s)
Online business
Industry/Entity Type
Video production
Contact Information for Business Card
Name of the company (Brightlane) , my name (Mathis Verlaeken) and the little square for QR code at the back

```html
<!DOCTYPE html>
<html lang="en">
<head>
<meta charset="utf-8">
<title>Brightlane Business Card</title>
<link href="https://fonts.googleapis.com/css2?family=Poppins:wght@300;400;500;600&display=swap" rel="stylesheet">
<style>
  :root {
    --backdrop: #dedede;
    --card: #1f1f20;
    --gold: #e0bc3a;
    --white: #f4f4f4;
    --divider: #6b6b6b;
  }
  * { box-sizing: border-box; margin: 0; padding: 0; }
  html, body {
    width: 1200px; height: 900px; overflow: hidden;
    background: var(--backdrop);
    font-family: "Poppins", sans-serif;
  }
  .sheet {
    width: 1200px; height: 900px;
    display: flex; flex-direction: column;
    align-items: center; justify-content: center; gap: 56px;
  }
  .card {
    width: 630px; height: 360px;
    background: var(--card);
    border-radius: 26px;
    position: relative;
    overflow: hidden;
  }
  /* front */
  .card--front { display: flex; align-items: center; }
  .brand {
    display: flex; align-items: center; gap: 10px;
    color: var(--gold);
    font-weight: 500;
    letter-spacing: 0.5px;
    white-space: nowrap;
  }
  .brand__dot {
    border-radius: 50%;
    background: var(--gold);
    flex: none;
  }
  .front__brand-area {
    width: 330px; display: flex; justify-content: center;
  }
  .front__brand-area .brand { font-size: 40px; }
  .front__brand-area .brand__dot { width: 14px; height: 14px; }
  .front__divider {
    width: 1px; height: 190px; background: var(--divider); flex: none;
  }
  .contact {
    padding-left: 26px;
    color: var(--white);
    font-size: 13.5px; line-height: 1.45;
    white-space: nowrap;
  }
  .contact__name {
    color: var(--gold);
    font-size: 20px; font-weight: 600; line-height: 1.2;
  }
  .contact__role { font-size: 14px; font-weight: 400; margin-bottom: 6px; }
  .contact__address { margin-bottom: 6px; }
  .contact__line { display: flex; align-items: center; gap: 9px; }
  .contact__icon { width: 13px; height: 13px; flex: none; }
  .contact__icon path, .contact__icon rect, .contact__icon circle {
    fill: none; stroke: var(--gold); stroke-width: 1.6; stroke-linecap: round; stroke-linejoin: round;
  }
  /* back */
  .card--back { display: flex; align-items: center; justify-content: center; }
  .card--back .brand { font-size: 64px; gap: 16px; }
  .card--back .brand__dot { width: 22px; height: 22px; }
  .qr-slot {
    position: absolute;
    right: 32px; bottom: 32px;
    width: 72px; height: 72px;
    border: 2px solid var(--gold);
    border-radius: 6px;
  }
</style>
</head>
<body>
<main class="sheet">

  <section class="card card--front" aria-label="Business card front">
    <div class="front__brand-area">
      <div class="brand"><span class="brand__dot"></span>Brightlane</div>
    </div>
    <div class="front__divider"></div>
    <div class="contact">
      <p class="contact__name">Mathis Verlaeken</p>
      <p class="contact__role">Founder &amp; CEO</p>
      <p class="contact__address">4120 Harbor Row<br>Millbrook, Oregon 97012</p>
      <p class="contact__line">
        <svg class="contact__icon" viewBox="0 0 16 16" aria-hidden="true"><path d="M3 1.5h3l1.2 3.2-1.8 1.2a8 8 0 0 0 4.7 4.7l1.2-1.8 3.2 1.2v3a1.5 1.5 0 0 1-1.6 1.5A13 13 0 0 1 1.5 3.1 1.5 1.5 0 0 1 3 1.5z"/></svg>
        555-210-4831
      </p>
      <p class="contact__line">
        <svg class="contact__icon" viewBox="0 0 16 16" aria-hidden="true"><rect x="4" y="1" width="8" height="14" rx="1.5"/><path d="M7 12.5h2"/></svg>
        555-372-9105
      </p>
      <p class="contact__line">
        <svg class="contact__icon" viewBox="0 0 16 16" aria-hidden="true"><rect x="1.5" y="6" width="13" height="8" rx="1"/><rect x="4.5" y="1.5" width="7" height="4.5"/><path d="M4.5 10h7"/></svg>
        555-648-2276
      </p>
      <p class="contact__line">
        <svg class="contact__icon" viewBox="0 0 16 16" aria-hidden="true"><rect x="1.5" y="3" width="13" height="10" rx="1"/><path d="M1.5 4l6.5 5 6.5-5"/></svg>
        info@brightlane.com
      </p>
      <p class="contact__line">
        <svg class="contact__icon" viewBox="0 0 16 16" aria-hidden="true"><circle cx="8" cy="8" r="6.5"/><path d="M1.5 8h13M8 1.5c2.2 2 2.2 11 0 13M8 1.5c-2.2 2-2.2 11 0 13"/></svg>
        www.brightlane.com
      </p>
    </div>
  </section>

  <section class="card card--back" aria-label="Business card back">
    <div class="brand"><span class="brand__dot"></span>Brightlane</div>
    <div class="qr-slot" role="img" aria-label="Reserved square for QR code"></div>
  </section>

</main>
</body>
</html>
```